Business Card Design

New business card design

Target Market(s)

Residential & Commercial Property Managers

Industry/Entity Type

Plumbing Services

Contact Information for Business Card

Name - Rowan Keddle, title - Director, Phone Number - 0431 286 517, email - rowan@tbk-plumbing.com.au, Company ABN - 73 215 904 386,

Font styles to use
Sans Serif

Colors
0054AA
0677BA
7BADD7
CADEEF
E8F1F8

```html
<!DOCTYPE html>
<html lang="en">
<head>
<meta charset="utf-8">
<title>TBK Plumbing Services – Business Card</title>
<link rel="stylesheet" href="https://fonts.googleapis.com/css2?family=Arimo:wght@400;700&display=swap">
<style>
  :root {
    --backdrop: #e3e3e3;
    --card-white: #f4f4f5;
    --card-dark: #1d232a;
    --accent-blue: #0aa3e3;
    --ink-dark: #1d232a;
    --text-light: #ffffff;
    --mark-muted: #2c343c;
  }
  html, body {
    margin: 0;
    padding: 0;
    width: 1200px;
    height: 1040px;
    overflow: hidden;
    background: var(--backdrop);
    font-family: "Arimo", Arial, sans-serif;
  }
  .canvas {
    position: relative;
    width: 1200px;
    height: 1040px;
  }
  .card {
    position: absolute;
    left: 280px;
    width: 640px;
    height: 366px;
    border-radius: 16px;
    overflow: hidden;
  }
  .card--front { top: 130px; background: var(--card-white); }
  .card--back  { top: 567px; background: var(--card-dark); }

  .card__wave {
    position: absolute;
    inset: 0;
    width: 100%;
    height: 100%;
  }

  .brand {
    position: absolute;
    left: 47px;
    top: 40px;
    color: var(--ink-dark);
    font-weight: 400;
  }
  .brand__name {
    display: flex;
    align-items: center;
    gap: 10px;
    font-size: 72px;
    line-height: 1;
    letter-spacing: 4px;
  }
  .brand__dot {
    width: 16px;
    height: 16px;
    border-radius: 50%;
    background: var(--accent-blue);
    margin-top: 30px;
  }
  .brand__tagline {
    margin-top: 14px;
    font-size: 12px;
    letter-spacing: 11.5px;
  }

  .contact {
    position: absolute;
    right: 51px;
    top: 178px;
    text-align: right;
    color: var(--text-light);
  }
  .contact__name {
    margin: 0;
    font-size: 26px;
    font-weight: 700;
    color: var(--accent-blue);
    line-height: 1.2;
  }
  .contact__title {
    margin: 6px 0 0;
    font-size: 15px;
  }
  .contact__abn {
    margin: 25px 0 0;
    font-size: 16px;
  }
  .contact__list {
    list-style: none;
    margin: 16px 0 0;
    padding: 0;
    font-size: 16px;
    line-height: 20px;
  }
  .contact__list li {
    display: flex;
    justify-content: flex-end;
    align-items: center;
    gap: 7px;
  }
  .contact__icon { width: 13px; height: 13px; flex: none; }

  .back__mark {
    position: absolute;
    left: 0;
    right: 0;
    top: 120px;
    text-align: center;
    font-size: 64px;
    letter-spacing: 4px;
    color: var(--mark-muted);
  }
  .back__web {
    position: absolute;
    left: 0;
    right: 0;
    top: 321px;
    text-align: center;
    font-size: 16px;
    color: var(--text-light);
  }
</style>
</head>
<body>
<main class="canvas">

  <section class="card card--front" aria-label="Business card front">
    <svg class="card__wave" viewBox="0 0 800 456" preserveAspectRatio="none" aria-hidden="true">
      <path fill="var(--accent-blue)" d="M0,283 C110,360 200,388 300,328 C420,256 520,100 640,72 C720,56 770,62 800,70 L800,456 L0,456 Z"/>
      <path fill="var(--card-dark)" stroke="#ffffff" stroke-width="3" d="M0,322 C100,380 210,400 310,340 C430,268 520,120 630,88 C710,66 760,72 802,84 L802,458 L-2,458 Z"/>
    </svg>

    <div class="brand">
      <div class="brand__name">tbk <span class="brand__dot"></span></div>
      <div class="brand__tagline">plumbing services</div>
    </div>

    <div class="contact">
      <h1 class="contact__name">Rowan Keddle</h1>
      <p class="contact__title">Director</p>
      <p class="contact__abn">ABN - 73 215 904 386</p>
      <ul class="contact__list">
        <li>0431 286 517
          <svg class="contact__icon" viewBox="0 0 24 24" aria-hidden="true"><path fill="var(--accent-blue)" d="M6.6 10.8c1.4 2.8 3.8 5.1 6.6 6.6l2.2-2.2c.3-.3.7-.4 1-.2 1.1.4 2.3.6 3.6.6.6 0 1 .4 1 1V20c0 .6-.4 1-1 1C10.6 21 3 13.4 3 4c0-.6.4-1 1-1h3.5c.6 0 1 .4 1 1 0 1.3.2 2.5.6 3.6.1.3 0 .7-.2 1L6.6 10.8z"/></svg>
        </li>
        <li>rowan@tbk-plumbing.com.au
          <svg class="contact__icon" viewBox="0 0 24 24" aria-hidden="true"><rect x="2" y="5" width="20" height="14" fill="var(--accent-blue)"/><path d="M2 5l10 8 10-8" fill="none" stroke="var(--card-dark)" stroke-width="1.6"/></svg>
        </li>
      </ul>
    </div>
  </section>

  <section class="card card--back" aria-label="Business card back">
    <div class="back__mark">tbk</div>
    <div class="back__web">www.tbk-plumbing.com</div>
  </section>

</main>
</body>
</html>
```